Business card for a new innovative and professional lawn care business

We need a business card design for a new lawn care business in Halifax NS Canada. We offer lawn services in Halifax & Bedford. Our services offered include lawn care, garden services, and property maintenance. We take pride in our work and are experienced at what we do. I would like to see a design that is double sided. On the backside I would like the something simple (maybe my logo preferably on blackround (linked below) with website link, Facebook page or something). The front I want to include contact info:
Morgan Pell
phone 902-555-0148
email - brookvaleyards.ca
facebook - @brookvaleyards
Instagram maybe ? - @brookvaleyard
Serving Halifax and Bedford for 5 years?
I don't want it to have too much information as I will be passing them out in aim to visit website, or call !
We do want it to include lawn care, garden services and property maintenance.
Basic, catchy, and modern looking !
Logo attached below !

Target Market(s)

Passing business cards to everyone I meet or interact with.

Industry/Entity Type

Lawn Care

Contact Information for Business Card

Double sided with some basic information, with catchy colours and easy to look at.

Font styles to use
Sans Serif

Requirements
Must have
• Must be double sided and have :
• Name, Phone, Email, FB, Website, and 3 main services offered - lawn care, property maintenance, garden services
Nice to have
• Would be nice to have instagram link if it goes well on there
Should not have
• Don't want too much writing or images that are distracting

```html
<!DOCTYPE html>
<html lang="en">
<head>
<meta charset="utf-8">
<title>Brookvale Yards – Business Card</title>
<link href="https://fonts.googleapis.com/css2?family=Open+Sans:wght@400;600;700;800&display=swap" rel="stylesheet">
<style>
  :root {
    --stage: #e9ece8;
    --card-black: #050505;
    --card-white: #ffffff;
    --lime: #8cc63f;
    --forest: #0f6b35;
    --forest-deep: #0b4f27;
    --mist: #e6efe8;
    --text-dark: #1d4a2a;
    --text-light: #f2f2f2;
  }
  * { box-sizing: border-box; margin: 0; padding: 0; }
  html, body { width: 1200px; height: 900px; overflow: hidden; }
  body {
    background: var(--stage);
    font-family: "Open Sans", Arial, sans-serif;
    position: relative;
  }
  .card {
    position: absolute;
    left: 280px;
    width: 640px;
    height: 366px;
    border-radius: 18px;
    overflow: hidden;
    box-shadow: 0 10px 26px rgba(0,0,0,.18);
  }

  /* Back side */
  .card-back { top: 56px; background: var(--card-black); color: var(--text-light); }
  .back-brand {
    position: absolute; left: 0; right: 0; top: 122px;
    display: flex; align-items: center; justify-content: center; gap: 14px;
  }
  .brand-dot { width: 22px; height: 22px; border-radius: 50%; background: var(--lime); }
  .back-brand .brand-name {
    font-weight: 800; font-size: 50px; letter-spacing: 1px;
    color: var(--lime); text-transform: uppercase; line-height: 1;
  }
  .social {
    position: absolute; display: flex; align-items: center; gap: 9px;
    font-size: 15px; font-weight: 600; color: var(--text-light); line-height: 1;
  }
  .social-mark { width: 13px; height: 13px; border-radius: 3px; background: var(--lime); }
  .social-secondary { right: 44px; top: 230px; }
  .social-primary { left: 34px; bottom: 28px; }

  /* Front side */
  .card-front { top: 478px; background: var(--card-white); }
  .edge-band {
    position: absolute; left: 0; top: 0; bottom: 0; width: 22px; background: var(--forest);
  }
  .edge-stripe {
    position: absolute; left: 28px; top: 0; bottom: 0; width: 2px; background: var(--lime);
  }
  .mower-decoration {
    position: absolute; right: 30px; top: 20px; width: 280px; height: 320px;
    border-radius: 20px;
    background: radial-gradient(ellipse at 55% 55%, var(--mist) 0%, rgba(230,239,232,.5) 55%, rgba(255,255,255,0) 75%);
  }
  .divider {
    position: absolute; left: 300px; right: 0; top: 226px; height: 1.5px; background: var(--lime);
  }
  .front-brand {
    position: absolute; left: 62px; top: 40px;
    font-weight: 800; font-size: 44px; line-height: 1; letter-spacing: 1px;
    color: var(--lime); text-transform: uppercase;
  }
  .holder-name {
    position: absolute; left: 62px; top: 118px;
    font-weight: 800; font-size: 30px; color: var(--forest-deep); text-transform: uppercase;
  }
  .contact-list {
    position: absolute; left: 62px; top: 162px; list-style: none;
    font-size: 16px; color: var(--text-dark); line-height: 24px;
  }
  .contact-list li { display: flex; align-items: center; gap: 8px; }
  .contact-list svg { width: 13px; height: 13px; fill: none; stroke: var(--lime); stroke-width: 2; }
  .services { position: absolute; left: 62px; top: 244px; }
  .services-title {
    font-weight: 700; font-size: 20px; color: var(--lime); text-transform: uppercase; letter-spacing: .5px;
  }
  .services-list { list-style: none; font-size: 16px; color: var(--text-dark); line-height: 22px; margin-top: 2px; }
  .services-list li::before {
    content: ""; display: inline-block; width: 7px; height: 7px; border-radius: 50%;
    background: var(--lime); margin-right: 8px; vertical-align: middle;
  }
</style>
</head>
<body>

<section class="card card-back" aria-label="Card back">
  <div class="back-brand">
    <span class="brand-dot"></span>
    <span class="brand-name">Brookvale Yards</span>
  </div>
  <div class="social social-secondary"><span class="social-mark"></span>@brookvaleyard</div>
  <div class="social social-primary"><span class="social-mark"></span>@brookvaleyards</div>
</section>

<section class="card card-front" aria-label="Card front">
  <div class="edge-band"></div>
  <div class="edge-stripe"></div>
  <div class="mower-decoration" role="img" aria-label="Faint lawn mower illustration"></div>
  <div class="divider"></div>

  <div class="front-brand">Brookvale Yards</div>
  <div class="holder-name">Morgan Pell</div>

  <ul class="contact-list">
    <li>
      <svg viewBox="0 0 14 14"><path d="M3 1.5l2 .5 1 3-1.5 1a7 7 0 0 0 3.5 3.5l1-1.5 3 1 .5 2c-1 1-2 1.5-3 1.5A10 10 0 0 1 1.5 4.5C1.5 3.5 2 2.5 3 1.5z"/></svg>
      902-555-0148
    </li>
    <li>
      <svg viewBox="0 0 14 14"><rect x="1.5" y="3" width="11" height="8" rx="1"/><path d="M1.5 3.5l5.5 4 5.5-4"/></svg>
      info@brookvaleyards.ca
    </li>
    <li>
      <svg viewBox="0 0 14 14"><circle cx="7" cy="7" r="5.5"/><path d="M1.5 7h11M7 1.5c2 2 2 9 0 11M7 1.5c-2 2-2 9 0 11"/></svg>
      www.brookvaleyards.ca
    </li>
  </ul>

  <div class="services">
    <div class="services-title">Services</div>
    <ul class="services-list">
      <li>Lawn care</li>
      <li>Garden services</li>
      <li>Property maintenance</li>
    </ul>
  </div>
</section>

</body>
</html>
```